Customer Value Leaflet

We need a bi-fold brochure designing, based on the attached PDF wireframes. Our company name is brambleharvik.com (of which the logo is currently being designed). The corporate colour is orange (the exact shade of which we are happy to leave to the designers discretion).

The leaflet will distributed to customer experience experts and marketers so the design needs to be bright, engaging, clean and simple. Design is critical.

It Company

```html
<!DOCTYPE html>
<html lang="en">
<head>
<meta charset="utf-8">
<title>Customer Value Leaflet – brambleharvik.com</title>
<link rel="stylesheet" href="https://fonts.googleapis.com/css2?family=Open+Sans:wght@400;700&display=swap">
<style>
  :root {
    --green: #15954a;
    --orange: #f8b041;
    --ink: #2b2b2b;
    --label-dark: #262626;
    --paper: #ffffff;
    --paper-tint: #f7f7f7;
  }
  * { box-sizing: border-box; margin: 0; padding: 0; }
  html, body { width: 1200px; height: 1200px; overflow: hidden; background: var(--paper); }
  .leaflet {
    position: relative;
    width: 1200px;
    height: 1200px;
    font-family: "Open Sans", Arial, sans-serif;
    color: var(--ink);
    background: var(--paper);
  }
  .top-band {
    position: absolute; left: 0; top: 0; width: 1200px; height: 147px;
    background: var(--green);
    color: var(--paper);
    font-size: 33px;
    display: flex; align-items: center; justify-content: center;
  }
  .side-panel {
    position: absolute; top: 147px; height: 336px;
    background: var(--paper-tint);
  }
  .side-panel.left { left: 0; width: 540px; }
  .side-panel.right { left: 660px; width: 540px; }
  .insight-band {
    position: absolute; left: 0; top: 483px; width: 1200px; height: 405px;
    background: var(--orange);
  }
  .flow-arrow { position: absolute; left: 0; top: 0; width: 1200px; height: 1200px; }
  .flow-label {
    position: absolute; left: 600px; top: 508px;
    transform: translate(-50%, -50%) rotate(-90deg);
    white-space: nowrap;
    color: var(--paper);
    font-size: 28px;
    letter-spacing: 1px;
  }
  .customer-card { position: absolute; top: 205px; height: 245px; display: flex; }
  .customer-card.kim { left: 50px; }
  .customer-card.kevin { left: 703px; }
  .customer-name {
    width: 125px; height: 100%;
    background: var(--label-dark);
    position: relative;
  }
  .customer-name span {
    position: absolute; left: 50%; top: 50%;
    transform: translate(-50%, -50%) rotate(-90deg);
    color: var(--paper);
    font-weight: 700;
    font-size: 30px;
  }
  .customer-value {
    width: 322px; height: 100%;
    background: var(--orange);
    display: flex; align-items: center; justify-content: center;
    text-align: center;
    font-size: 60px;
    line-height: 1.2;
  }
  .insight {
    position: absolute; top: 565px; width: 460px;
    text-align: center;
    font-size: 35px;
    line-height: 48px;
  }
  .insight.kim { left: 45px; }
  .insight.kevin { left: 695px; }
  .closing {
    position: absolute; left: 0; top: 980px; width: 1200px;
    text-align: center;
    font-size: 35px;
    line-height: 47px;
  }
  .closing strong { font-weight: 700; }
</style>
</head>
<body>
<main class="leaflet">
  <header class="top-band">Once you can calculate CLV…</header>

  <div class="side-panel left"></div>
  <div class="side-panel right"></div>
  <div class="insight-band"></div>

  <svg class="flow-arrow" viewBox="0 0 1200 1200" aria-hidden="true">
    <polygon fill="var(--green)" points="555,140 645,140 645,842 737,842 600,942 463,842 555,842"/>
  </svg>
  <div class="flow-label">OPTIMISE YOUR MARKETING</div>

  <section class="customer-card kim">
    <div class="customer-name"><span>KIM</span></div>
    <div class="customer-value">CLV of<br>£149</div>
  </section>
  <section class="customer-card kevin">
    <div class="customer-name"><span>KEVIN</span></div>
    <div class="customer-value">CLV of<br>£282</div>
  </section>

  <p class="insight kim">you can personalise Kim’s marketing experience to grow her lifetime value to be more like Kevin’s</p>
  <p class="insight kevin">you can understand why Kevin is more valuable and acquire more customers<br>like him</p>

  <footer class="closing">
    We use data and science to predict how your customers<br>
    will behave in future. Even if you already use CLV we<br>
    an help you do and earn more… <strong>brambleharvik.com</strong>
  </footer>
</main>
</body>
</html>
```